Premium Business Card for Wealth Creation

Please see attached business card for example.
Happy to look at options like Blue background with Yellow
Target Market(s)
People who want to buy investment property or create wealth
Industry/Entity Type
Investment
Contact Information for Business Card
Tel: 1800 314 579
Mobile: 0417 265 904
Address: Level 1, 64 Carrow Lane Brighton Vic 3186
Name: Martin Feldway
Title: CEO
Website: www.quolvane.com.au
Email: martin@quolvane.com.au
Font styles to use
Sans Serif
Colors
0255a3
fbed22
Requirements
Must have
- Look great

```html
<!DOCTYPE html>
<html lang="en">
<head>
<meta charset="utf-8">
<title>Quolvane Business Card</title>
<link rel="stylesheet" href="https://fonts.googleapis.com/css2?family=Open+Sans:wght@400;600;700;800&display=swap">
<style>
  :root {
    --brand-blue: #0255a3;
    --band-blue: #3f63c0;
    --brand-yellow: #fbed22;
    --accent-yellow: #f2cd1c;
    --card-white: #ffffff;
    --backdrop: #e9e6e1;
    --text-blue: #2f55b8;
  }
  * { margin: 0; padding: 0; box-sizing: border-box; }
  html, body { width: 1200px; height: 780px; overflow: hidden; }
  body {
    background: var(--backdrop);
    font-family: "Open Sans", Arial, sans-serif;
    position: relative;
  }
  .card {
    position: absolute;
    width: 540px;
    height: 310px;
    background: var(--card-white);
    border-radius: 4px;
    box-shadow: 0 3px 0 #d8d8d8, 0 6px 0 #cfcfcf, 0 14px 30px rgba(0,0,0,0.18);
    overflow: hidden;
  }
  .card-front { left: 50px; top: 80px; }
  .card-back { left: 610px; top: 390px; }
  .front-curve { position: absolute; inset: 0; }
  .brand-mark {
    display: flex;
    align-items: center;
    gap: 12px;
    color: var(--text-blue);
    font-weight: 800;
    letter-spacing: 0.5px;
  }
  .brand-dot {
    border-radius: 50%;
    background: var(--accent-yellow);
    flex: none;
  }
  .card-front .brand-mark { position: absolute; left: 34px; top: 40px; font-size: 38px; z-index: 1; }
  .card-front .brand-dot { width: 44px; height: 44px; }
  .contact-block {
    position: absolute;
    left: 88px;
    top: 116px;
    color: var(--text-blue);
    z-index: 1;
  }
  .person-name { font-size: 19px; font-weight: 700; line-height: 1.1; }
  .person-title { font-size: 13px; color: #d9b414; margin-bottom: 12px; }
  .address { font-size: 13px; line-height: 1.35; margin-bottom: 4px; }
  .contact-line {
    display: flex;
    align-items: center;
    gap: 7px;
    font-size: 13px;
    line-height: 1.5;
  }
  .contact-icon {
    width: 14px;
    height: 14px;
    flex: none;
  }
  .card-back .brand-mark {
    position: absolute;
    left: 50%;
    top: 50%;
    transform: translate(-50%, -50%);
    font-size: 54px;
    gap: 16px;
  }
  .card-back .brand-dot { width: 60px; height: 60px; }
</style>
</head>
<body>
  <section class="card card-front">
    <svg class="front-curve" viewBox="0 0 540 310" width="540" height="310" aria-hidden="true">
      <rect x="300" y="0" width="240" height="310" fill="var(--band-blue)"/>
      <path d="M330 0 C474 70 494 210 462 310 L0 310 L0 0 Z" fill="var(--card-white)"/>
      <path d="M330 0 C462 70 482 210 452 310 L0 310 L0 0 Z" fill="var(--accent-yellow)"/>
      <path d="M330 0 C428 70 440 210 410 310 L0 310 L0 0 Z" fill="var(--card-white)"/>
    </svg>
    <div class="brand-mark"><span class="brand-dot"></span>QUOLVANE</div>
    <div class="contact-block">
      <p class="person-name">Martin Feldway</p>
      <p class="person-title">CEO</p>
      <p class="address">Level 1, 64 Carrow Lane<br>Wendrell Vic 3194</p>
      <p class="contact-line">
        <svg class="contact-icon" viewBox="0 0 14 14" aria-label="Phone"><rect width="14" height="14" fill="var(--accent-yellow)"/><path d="M4 3 L6 3 L6.5 5 L5.5 6 Q6.5 8 8 8.5 L9 7.5 L11 8 L11 10 Q7 11 4 7 Q3 5 4 3 Z" fill="#fff"/></svg>
        1800 314 579
      </p>
      <p class="contact-line">
        <svg class="contact-icon" viewBox="0 0 14 14" aria-label="Mobile"><rect width="14" height="14" fill="var(--accent-yellow)"/><rect x="4.5" y="2.5" width="5" height="9" rx="1" fill="#fff"/></svg>
        0417 265 904
      </p>
      <p class="contact-line">
        <svg class="contact-icon" viewBox="0 0 14 14" aria-label="Email"><rect width="14" height="14" fill="var(--accent-yellow)"/><rect x="3" y="4" width="8" height="6" fill="#fff"/><path d="M3 4 L7 7.5 L11 4" stroke="var(--accent-yellow)" fill="none"/></svg>
        martin@quolvane.com.au
      </p>
    </div>
  </section>

  <section class="card card-back">
    <div class="brand-mark"><span class="brand-dot"></span>QUOLVANE</div>
  </section>
</body>
</html>
```